Small Business Directory Site Requires a Professional Responsive Web Design

Small Business Directory and Coupon Site - we require a complete website design for a brand new responsive & mobile friendly website. We already have a coder who will professional code our website in Magento.

All PSD pages need to be professionally designed then uploaded into a sharedrive (i.e. like filecrate). Additionally, as I cannot pre-empt everything, please note that we may require a little more assistance once the files have been transferred (for example, in www.brightlane-listings.example if you hover your mouse on the search box you will see a pop up box. We want one of these too and I think that means there may be extra design work here)

We have some draft page sketches have been created (there are some minor changes we want to the sketches provided though); however, we require an excellent designer to add the creative touches to it to make it look professionally created. All artwork/font must be legal.

-------------------------
We like the look of the www.brightlane-listings.example and www. marlowfolio.example

For the headers, please consider a font similar to RNS camellia. We likes this style, but it is too thin for the headers...so we need a variation like this one. For the copy/general text font, something basic that marries well with the headers.

---------------------

Please be sure to also read the brief we wrote for the coder as this will help with better understanding our design requirements.

In total I believe we have about 50 pages. This includes all the little pages and most of the pop up boxes (but not the little help key boxes). For example, pages include...

1. Login (this is where customers log in and can edit, manage their profiles. This means that there are backend membership pages)
2. Mini Services (same look and feel as the business coupons)
3. Resource Centre
4. Join (this is where customers learn about the packages available to submit a directory listing, if they ‘buy’ a package (i.e. free, $25 or $150 package) then they can create their own directory listing)
5. Search the directory (customer can view all the categories and also search the directory)
6. Create a directory listing (this is where customers learn about the packages available to submit a directory listing, if they ‘buy’ a package (i.e. free, $25 or $150 package) then they can create their own directory listing)
7. Quote finder (also know as Get a Quote)
8. Coupons (customer go to the business coupon page and can view all current coupons/submit a coupon)
9. Submit a coupon (form)
10.Advertise with us (form)
11. Join the forum
12.Submit an article or video (form)
13. Affiliates (listing of affiliates we currently have)
14. Become an affiliate (form)
15. Case studies (customer can view the case studies we have in the resource centre)
16. Help Guides (customer can view the help guides we have in the resource centre)
17. About Us
18 .Contact Us (form)
19. Terms & Condition
20. Privacy Policy
21. Supporting City Councils
22. Site Map
23. Forgot password / login details
24. Homepage
25. If we hover over a few areas (i.e. search box, location field) it pops up with more information.
etc etc etc. . . there are more pages.

Please see our filecrate link for the draft mock up pages that I have created so far.

https://www.cloudtrunk.example/sh/qk72pmw4rtz8nd/KLMvbTq2fWndxPzs8Yh4ecRQu

We are in a rush! We'd like to get the majority of the artwork completed by the end of the month. Minor fixes/tweaks can occur thereafter.

Target Market(s)

Small Businesses (employees 0 - 50) located throughout Australia

Industry/Entity Type

Business

Font styles to use
Sans Serif

Requirements
Must have
• Professional. Artwork must be legal (cannot be cut and paste or taken off other websites, must be legally purchased and used).Must look contemporary, fresh, modern.

Absolutely must be a responsive site!
Nice to have
• original work, original photos, original art.

like modern, fresh photos that demonstrate innovation, growth, small business, Australian scenery, stability, goals/passion.
Should not have
• cut and paste graphics, illegal graphics, not purchased graphics.

```html
<!DOCTYPE html>
<html lang="en">
<head>
<meta charset="utf-8">
<title>Tradeside Hub – Small Business Directory</title>
<link rel="stylesheet" href="https://fonts.googleapis.com/css2?family=Roboto:wght@300;400;500;700&display=swap">
<style>
:root{
  --black:#000;
  --ink:#222;
  --orange:#f7941d;
  --white:#fff;
  --grey-band:#ececec;
  --card-grey:#c9c9c9;
  --bar-grey:#8a8a8a;
  --button-grey:#5a5a5a;
  --footer-base:#1b1b1b;
  --muted:#cfcfcf;
}
*{box-sizing:border-box;margin:0;padding:0}
html,body{width:1060px;height:1200px;overflow:hidden;background:var(--white)}
body{position:relative;font-family:'Roboto',sans-serif;color:var(--ink)}
.abs{position:absolute}

/* header */
.site-header{left:0;top:0;width:1060px;height:94px;background:var(--black)}
.brand{left:154px;top:34px;display:flex;align-items:center;gap:8px}
.brand-mark{width:22px;height:22px;border-radius:50%;background:var(--orange)}
.brand-name{color:var(--white);font-size:19px;font-weight:500;letter-spacing:.3px}
.main-nav{left:438px;top:41px;display:flex;gap:15px}
.main-nav a{color:var(--white);text-decoration:none;font-size:12.5px}

/* hero */
.hero{left:0;top:94px;width:1060px;height:416px;
  background:linear-gradient(180deg,#16203a 0%,#223763 38%,#3a5a8a 60%,#1b2a48 80%,#0e1524 100%)}
.hero-title{left:155px;top:186px;color:var(--white);font-size:39px;font-weight:500}
.hero-sub{left:155px;top:234px;color:var(--white);font-size:21px;font-weight:400;letter-spacing:1px}
.search-bar{left:154px;top:278px;width:474px;height:64px;background:var(--orange);border-radius:3px}
.search-field{position:absolute;top:15px;height:34px;background:var(--white);
  font-size:9px;color:#333;padding:11px 9px}
.search-what{left:13px;width:213px}
.search-where{left:276px;width:136px}
.search-near{position:absolute;left:241px;top:27px;font-size:10px;color:#5a3200}
.search-icon{position:absolute;left:427px;top:17px}
.join-btn{left:487px;top:365px;width:140px;height:38px;background:#0b0b0b;border-radius:3px;
  color:var(--white);font-size:16px;text-align:center;line-height:38px;box-shadow:0 2px 4px rgba(0,0,0,.5)}
.listing-card{left:688px;top:157px;width:216px;height:262px;background:var(--card-grey);border:2px solid var(--black)}
.listing-card h3{position:absolute;left:0;top:12px;width:100%;text-align:center;font-size:15px;font-weight:500;line-height:18px;color:#1a1a1a}
.plan{position:absolute;left:27px;top:68px;width:160px;height:178px;background:var(--white)}
.plan-inner{position:absolute;left:10px;top:12px;width:140px;height:156px;border:2px solid #bbb;border-radius:3px}
.plan-price{position:absolute;left:-6px;top:0;width:148px;height:26px;background:var(--bar-grey);
  color:var(--white);font-size:15px;font-weight:700;display:flex;align-items:center;padding-left:20px;gap:6px;white-space:nowrap}
.plan-price small{font-size:8px;font-weight:500}
.plan-tick{flex:none;width:14px;height:14px;border-radius:50%;background:var(--white)}
.plan-type{position:absolute;top:42px;width:100%;text-align:center;font-size:8px;font-weight:700;color:#111}
.plan-feats{position:absolute;top:62px;width:100%;text-align:center;font-size:7px;line-height:11.5px;color:#888}
.pay-btn{position:absolute;left:30px;top:126px;width:76px;height:13px;border-radius:7px;background:var(--button-grey);
  font-size:7px;font-weight:500;color:var(--white);text-align:center;line-height:13px}
.card-arrow{position:absolute;top:139px;width:18px;height:42px;background:#d8d8d8}
.card-arrow.prev{left:16px}.card-arrow.next{left:176px}
.slider-dots{left:1024px;top:309px;display:flex;flex-direction:column;gap:11px}
.slider-dots span{width:8px;height:8px;border-radius:50%;background:var(--white)}
.slider-dots span:first-child{background:var(--orange)}

/* community */
.section-title{left:0;top:540px;width:1060px;text-align:center;color:var(--orange);font-size:17px;font-weight:400}
.feature{top:592px;width:216px}
.feature h4{font-size:14px;font-weight:400;color:#444;height:39px}
.feature-media{width:214px;height:124px}
.feature p{font-size:9.5px;line-height:14.5px;color:#333;margin-top:16px;text-align:justify}
.media-photo{background:linear-gradient(135deg,#e9eef4 0%,#b9c8d8 45%,#6f87a3 100%)}
.media-video{background:#2f2f2f;display:flex;align-items:center;justify-content:center}
.media-partner{display:flex;align-items:center;justify-content:center;gap:8px;color:#1d3d78;font-size:19px;font-weight:700;white-space:nowrap}
.media-partner .dot{flex:none;width:28px;height:28px;border-radius:50%;background:#1e88d0}

/* partners */
.partner-band{left:0;top:858px;width:1060px;height:110px;background:var(--grey-band)}
.partner{top:34px;width:220px;text-align:center;font-size:30px;font-weight:700;white-space:nowrap}
.partner.p1{left:148px;color:#1a1a1a}
.partner.p2{left:418px;color:#3c3c3c}
.partner.p3{left:696px;color:#1565c0}

/* footer */
.site-footer{left:0;top:968px;width:1060px;height:172px;background:var(--black)}
.foot-col{top:21px}
.foot-col h5{color:var(--orange);font-size:14px;font-weight:500;margin-bottom:12px}
.foot-col a{display:block;color:var(--white);text-decoration:none;font-size:11px;line-height:19.7px}
.social{display:flex;gap:14px}
.social-item{display:flex;flex-direction:column;align-items:center;gap:3px}
.social-item span{width:32px;height:32px;border-radius:50%;border:3px solid #ddd}
.social-item em{font-style:normal;font-size:7px;color:var(--muted)}
.copyright-bar{left:0;top:1140px;width:1060px;height:60px;background:var(--footer-base);
  color:var(--muted);font-size:11px;text-align:center;line-height:60px}
</style>
</head>
<body>

<header class="site-header abs">
  <div class="brand abs"><span class="brand-mark"></span><span class="brand-name">Tradeside Hub</span></div>
  <nav class="main-nav abs">
    <a href="#">Login</a><a href="#">Join</a><a href="#">Coupounts</a><a href="#">Mini Services</a>
    <a href="#">Get a Quote</a><a href="#">Advertise</a><a href="#">Resoure Centre</a>
  </nav>
</header>

<section class="hero abs" role="img" aria-label="Night photograph of a lit suspension bridge over a harbour with old timber pylons in the water"></section>
<h1 class="hero-title abs">It's a Brand New Day</h1>
<p class="hero-sub abs">DO MORE OF WHAT YOU LOVE</p>

<form class="search-bar abs">
  <div class="search-field search-what">What are vou looking for?</div>
  <span class="search-near">near</span>
  <div class="search-field search-where">Where?</div>
  <svg class="search-icon" width="30" height="30" viewBox="0 0 30 30" aria-label="Search">
    <circle cx="12" cy="12" r="8" fill="none" stroke="#fff" stroke-width="3"/>
    <line x1="18" y1="18" x2="26" y2="26" stroke="#fff" stroke-width="4" stroke-linecap="round"/>
  </svg>
</form>
<div class="join-btn abs">Join Us Today</div>

<aside class="listing-card abs">
  <h3>Create a directory<br>listing today</h3>
  <div class="plan">
    <div class="plan-inner">
      <div class="plan-price"><span class="plan-tick"></span>A$25<small>/YEAR</small></div>
      <div class="plan-type">3 CATEGORY LISTING</div>
      <div class="plan-feats">Promote Your Special Offers<br>Business Profile &amp; Logo<br>Website &amp; Email Link</div>
      <div class="pay-btn">Checkout</div>
    </div>
  </div>
  <svg class="card-arrow prev" viewBox="0 0 18 42"><polyline points="12,8 5,21 12,34" fill="none" stroke="#222" stroke-width="2"/></svg>
  <svg class="card-arrow next" viewBox="0 0 18 42"><polyline points="6,8 13,21 6,34" fill="none" stroke="#222" stroke-width="2"/></svg>
</aside>
<div class="slider-dots abs"><span></span><span></span><span></span><span></span><span></span></div>

<h2 class="section-title abs">GET REAL SUPPORT FROM OUR COMMUNITY</h2>

<article class="feature abs" style="left:154px">
  <h4>How Did You Sort Your Business?</h4>
  <div class="feature-media media-photo" role="img" aria-label="Close-up of a calculator and pen resting on financial charts"></div>
  <p>Learn from Mara Collins, a real small business owner. How she started her business and what are the most valuable resources for her right now.</p>
</article>

<article class="feature abs" style="left:422px">
  <h4>Why Go with Tradeside Hub?</h4>
  <div class="feature-media media-video">
    <svg width="44" height="44" viewBox="0 0 44 44" aria-label="Play video">
      <circle cx="22" cy="22" r="20" fill="#555"/><polygon points="17,13 32,22 17,31" fill="#fff"/>
    </svg>
  </div>
  <p>What small business owner can't relate to the ongoing task of attracting new customers? Struggling with cash flow? Or how about not And that's where we come in.</p>
</article>

<article class="feature abs" style="left:689px">
  <h4>Become an Affiliate</h4>
  <div class="feature-media media-partner"><span class="dot"></span>Harbourline Cover</div>
  <p>If you have a network of small businesses, let us help to create additional value for your members and make money for your network. Talk to us today about how we can help.</p>
</article>

<section class="partner-band abs">
  <div class="partner p1 abs">Hollinmere</div>
  <div class="partner p2 abs">Tessaline</div>
  <div class="partner p3 abs">Varrowick</div>
</section>

<footer class="site-footer abs">
  <div class="foot-col abs" style="left:157px">
    <h5>Site Directy</h5>
    <a href="#">Search the Directry</a><a href="#">Create a Directry listing</a><a href="#">Quote Finder</a>
    <a href="#">Submit a Coupon</a><a href="#">Advertise With Us</a>
  </div>
  <div class="foot-col abs" style="left:300px">
    <h5>Resourose</h5>
    <a href="#">Join the forum</a><a href="#">submit an article or video</a><a href="#">Affect</a>
    <a href="#">Become an affect</a><a href="#">case studies</a>
  </div>
  <div class="foot-col abs" style="left:452px">
    <h5>Popular Categoires</h5>
    <a href="#">Search the Directry</a><a href="#">Create a Directry listing</a><a href="#">Quote Finder</a>
    <a href="#">Submit a Coupon</a><a href="#">Advertise With Us</a>
  </div>
  <div class="foot-col abs" style="left:605px">
    <h5>About</h5>
    <a href="#">About us</a><a href="#">Contact us</a><a href="#">Terms &amp; Conditions</a>
    <a href="#">Supporting by cound</a><a href="#">site map</a>
  </div>
  <div class="foot-col abs" style="left:740px">
    <h5>Follow us</h5>
    <div class="social">
      <div class="social-item"><span style="background:#3b5998"></span><em>Palvo</em></div>
      <div class="social-item"><span style="background:#1da1f2"></span><em>Chirrin</em></div>
      <div class="social-item"><span style="background:#d34836"></span><em>Gyrel</em></div>
      <div class="social-item"><span style="background:#1e88c8"></span><em>Tenvo</em></div>
    </div>
  </div>
</footer>
<div class="copyright-bar abs">Copyright © 2014 All rights reserved.</div>

</body>
</html>
```